Professional & attention grabbing.

A business card design, front and back. I already have a logo I will attach, but I am open to something new as well.
Things to include:
Name:
Title:
Phone:
Email:
Wanting something that is professional but attention grabbing.
Also we do a lot of work using drones on natural gas pipelines (leading the future)if you want to include any of that. I'm open to ideas.
Target Market(s)
Natural gas transmission industry / greenhouse gas mitigation industry
Industry/Entity Type
Business
Colors
Designer to choose colors to be used in the design.
Look and feel
Each slider illustrates characteristics of the customer's brand and the style your logo design should communicate.

```html
<!DOCTYPE html>
<html lang="en">
<head>
<meta charset="utf-8">
<title>Kestrel Vale Inspections — Business Card</title>
<link rel="stylesheet" href="https://fonts.googleapis.com/css2?family=Source+Sans+3:wght@400;600;700&display=swap">
<style>
  :root {
    --page-bg: #e4e4e4;
    --card-light: #ffffff;
    --card-dark: #363638;
    --brand-red: #c01f26;
    --ink: #3a3a3c;
    --ink-soft: #555558;
    --wash-gray: #ececec;
    --wash-pink: #f8e4e6;
    --on-dark: #ffffff;
  }
  * { box-sizing: border-box; margin: 0; padding: 0; }
  html, body {
    width: 1200px; height: 987px; overflow: hidden;
    background: var(--page-bg);
    font-family: "Source Sans 3", "Myriad Pro", Arial, sans-serif;
  }
  .card {
    position: absolute; left: 293px; width: 615px; height: 352px;
    overflow: hidden;
  }
  .card--front { top: 130px; background: var(--card-light); }
  .card--back { top: 505px; background: var(--card-dark); }

  .front-wash {
    position: absolute; right: 0; top: 0; width: 330px; height: 352px;
    background: linear-gradient(160deg, var(--wash-pink) 0%, var(--wash-gray) 45%, #f4f4f4 100%);
    border-top-left-radius: 330px 352px;
    opacity: .85;
  }

  .brand-lockup {
    position: absolute; left: 0; top: 42px;
    display: flex; align-items: center; gap: 14px;
  }
  .brand-lockup__square {
    width: 26px; height: 90px; background: var(--brand-red);
  }
  .brand-lockup__name {
    font-weight: 700; font-size: 30px; line-height: 1.05;
    color: var(--ink); text-transform: uppercase; letter-spacing: .5px;
  }

  .person { position: absolute; left: 138px; top: 170px; }
  .person__name {
    font-weight: 600; font-size: 23px; color: var(--brand-red);
    letter-spacing: .3px; line-height: 1;
  }
  .person__title {
    margin-top: 9px; font-size: 17px; color: var(--ink); line-height: 1;
  }

  .contact-list { position: absolute; left: 138px; top: 243px; list-style: none; }
  .contact-list li {
    display: flex; align-items: center; gap: 9px;
    font-size: 16.5px; color: var(--ink-soft); height: 23.5px;
  }
  .contact-list svg { width: 15px; height: 15px; fill: var(--brand-red); flex: none; }

  .back-lockup {
    position: absolute; left: 0; right: 0; top: 112px;
    display: flex; justify-content: center; align-items: center; gap: 16px;
  }
  .back-lockup__square { width: 34px; height: 34px; background: var(--brand-red); }
  .back-lockup__name {
    font-weight: 700; font-size: 36px; color: var(--on-dark);
    text-transform: uppercase; letter-spacing: 1px;
  }
  .back-web {
    position: absolute; left: 0; right: 0; top: 302px; text-align: center;
    font-style: normal; font-size: 17px; letter-spacing: 4px; color: var(--on-dark);
  }
</style>
</head>
<body>
  <section class="card card--front" aria-label="Business card front">
    <div class="front-wash"></div>
    <div class="brand-lockup">
      <span class="brand-lockup__square"></span>
      <span class="brand-lockup__name">Kestrel Vale<br>Inspections</span>
    </div>
    <div class="person">
      <p class="person__name">DANA WHITFIELD</p>
      <p class="person__title">CEO/FOUNDER</p>
    </div>
    <ul class="contact-list">
      <li>
        <svg viewBox="0 0 16 16" aria-hidden="true"><path d="M3.6 1.2l2.3 2.6-1.3 1.8c.9 2 2.6 3.7 4.6 4.6l1.8-1.3 2.6 2.3-1.4 2.4C6.7 13.4 2.6 9.3 1.2 3.8z"/></svg>
        555 014 2290
      </li>
      <li>
        <svg viewBox="0 0 16 16" aria-hidden="true"><path d="M1 3.5h14v9H1zM1.8 4.3L8 9l6.2-4.7" stroke="#fff" stroke-width="1"/></svg>
        dana@kestrelvale.com
      </li>
      <li>
        <svg viewBox="0 0 16 16" aria-hidden="true"><circle cx="8" cy="8" r="7"/><path d="M1.5 8h13M8 1.2c-2.5 3-2.5 10.6 0 13.6M8 1.2c2.5 3 2.5 10.6 0 13.6" stroke="#fff" stroke-width=".9" fill="none"/></svg>
        www.kestrelvale.com
      </li>
    </ul>
  </section>

  <section class="card card--back" aria-label="Business card back">
    <div class="back-lockup">
      <span class="back-lockup__square"></span>
      <span class="back-lockup__name">Kestrel Vale</span>
    </div>
    <p class="back-web">www.kestrelvale.com</p>
  </section>
</body>
</html>
```